I'm looking for a rack card or trifold brochure to advertise elective ultrasounds

I need something that looks professional but eye catching to bring to doctor's office for display. I want it to have my logo, some 3D images and have a cohesive design. I want it to give a summary of what I offer in terms of elective ultrasounds: Peace of mind, early gender, 3D/4D. It should also mention that I can travel to the patient for in-home ultrasounds. (size around 4 x 9" rack card or trifold brochure)

Target Market(s)

Expecting moms and families

Industry/Entity Type

Elective 3D 4D private ultrasounds

Colors
E54698
E96AAD
F1A4CE
F9D9EA
FCEFF6

Requirements
Must have
• A focus on the elective portion of my business--offering the most amazing 3D images around (maybe not those words exactly). Offering on site and in-home services. Packages include Peace of Mind, Early gender, and 3D/4D imaging. Professional and experienced sonographer with 15+ years experience. Include 3d images. For this brochure, I don't want to mention the diagnostics portion as I will be bringing them to OBGYN office to hopefully display. I would like a "What we offer" section including -Conveniently located in Troy, NY or book in your home! -Early peace of mind ultrasounds starting at 6 weeks -Early gender determination starting at 13 weeks -A large, comfortable viewing space to bring your family. Kids are always welcome! -Top of the line technology to guarantee you will get the best possible images of your baby -Discounts for repeat families in the same pregnancy -Heartbeat animals to record baby's heartbeat -Gender reveal extinguishers, cannons, and balloons -3D face to Realistic AI transformation I would prefer for my face not to be on the brochure.
Nice to have
• A QR code linking the website
Should not have
• A sloppy presentation, I do not want to mention the diagnostic side of the business in these advertisements

```html
<!DOCTYPE html>
<html lang="en">
<head>
<meta charset="utf-8">
<title>Roaming Bump Ultrasound – Trifold</title>
<link href="https://fonts.googleapis.com/css2?family=Mali:wght@600&family=Mulish:wght@500;600;700;800&display=swap" rel="stylesheet">
<style>
  :root{
    --pink:#E54698;
    --pink-mid:#E96AAD;
    --pink-soft:#F1A4CE;
    --pink-pale:#F9D9EA;
    --pink-mist:#FCEFF6;
    --ink:#111111;
    --white:#ffffff;
    --hand:"Mali", cursive;
    --sans:"Mulish", sans-serif;
  }
  *{margin:0;padding:0;box-sizing:border-box}
  html,body{width:1200px;height:927px;overflow:hidden;background:#fff}
  .brochure{position:relative;width:1200px;height:927px;overflow:hidden;font-family:var(--sans);color:var(--ink)}

  /* Offer & about panel */
  .about{position:absolute;left:0;top:0;width:401px;height:927px;background:var(--pink);color:var(--white);
    display:flex;flex-direction:column;align-items:center;text-align:center;padding:18px 26px 0}
  .about__headline{font-family:var(--hand);font-weight:600;font-size:24px;line-height:32px}
  .section-title{font-size:20px;font-weight:700;letter-spacing:.5px;margin-top:16px}
  .offer-list{list-style:none;text-align:left;margin-top:10px;width:100%}
  .offer-list li{position:relative;padding-left:20px;font-size:13.2px;line-height:17px;font-weight:600;margin-bottom:6px}
  .offer-list li::before{content:"";position:absolute;left:2px;top:5px;width:8px;height:8px;border-radius:50%;background:var(--pink-pale)}
  .about__name{font-size:16px;line-height:22px;font-weight:600;margin-top:8px}
  .about__bio{font-size:12.6px;line-height:18px;font-weight:600;margin-top:10px}

  /* Scene behind middle & right panels */
  .scene{position:absolute;left:401px;top:0;width:799px;height:927px}
  .divider{position:absolute;left:800px;top:0;width:1px;height:927px;background:rgba(0,0,0,.08)}

  /* Packages */
  .packages__title{position:absolute;left:439px;top:16px;font-family:var(--hand);font-weight:600;font-size:27px;color:var(--white)}
  .package__photo{position:absolute;width:112px;height:112px;border-radius:50%;border:4px solid var(--pink-mist);
    background:radial-gradient(circle at 45% 45%,#e2a274 0%,#b6683f 55%,#3a1a10 100%)}
  .package__text{position:absolute;left:570px;color:var(--white)}
  .package__name{font-size:26px;line-height:30px;font-weight:600}
  .package__price{font-size:32px;line-height:40px;font-weight:800;margin-top:6px}
  .feature-photo{position:absolute;left:568px;top:482px;width:168px;height:168px;border-radius:50%;border:5px solid var(--pink-mist);
    background:radial-gradient(circle at 45% 45%,#e69a6c 0%,#b85a35 55%,#2a120a 100%)}

  /* Contact */
  .icon-disc{position:absolute;width:74px;height:74px;border-radius:50%;background:var(--pink);display:flex;align-items:center;justify-content:center}
  .contact__address{position:absolute;left:432px;top:696px;font-size:24px;line-height:30px;font-weight:700}
  .contact__phone{position:absolute;left:432px;top:868px;font-size:24px;font-weight:600}

  /* Cover */
  .cover__title{position:absolute;left:800px;top:24px;width:410px;text-align:center;color:var(--white);font-size:26px;line-height:32px;font-weight:600}
  .cover__tagline{color:var(--pink);font-weight:700}
  .brand{position:absolute;left:904px;top:537px;width:256px;height:256px;border-radius:50%;background:var(--white);
    border:6px solid var(--pink);display:flex;align-items:center;justify-content:center;text-align:center}
  .brand__name{font-size:24px;line-height:30px;font-weight:600;color:#2c2c2c}
  .call__label{position:absolute;left:800px;top:808px;width:400px;text-align:center;font-size:25px;font-weight:700}
  .call__number{position:absolute;left:800px;top:846px;width:400px;text-align:center;font-size:48px;font-weight:700;color:var(--pink)}
</style>
</head>
<body>
<div class="brochure">

  <section class="about">
    <h2 class="about__headline">Proudly Offering Elective<br>3D/4D Mobile Ultrasounds</h2>
    <h3 class="section-title">WHAT WE OFFER</h3>
    <ul class="offer-list">
      <li>Conveniently located in Troy, NY or book in your home!</li>
      <li>Early peace of mind ultrasounds starting at 6 weeks</li>
      <li>Early gender determination starting at 13 weeks</li>
      <li>A large, comfortable viewing space to bring your family. Kids are always welcome!</li>
      <li>Top of the line technology for the best possible images of your baby</li>
      <li>Discounts for repeat families in the same pregnancy</li>
      <li>Heartbeat animals to record baby's heartbeat</li>
      <li>Gender reveal extinguishers, cannons, and balloons</li>
      <li>3D face to Realistic AI transformation</li>
    </ul>
    <h3 class="section-title">ABOUT US</h3>
    <p class="about__name">Dana Whitfield, B.S., RDMS OB/GYN,<br>RDCS (FE), RT(R)</p>
    <p class="about__bio">I am a Registered Sonographer with over 15 years of experience in Obstetrics, and I have been blessed to be part of the journey of countless mothers-to-be. Bonding with your baby begins in the womb. Seeing baby's movements, facial features, cheeks, and toes creates an instant love. I have felt that same joy with my own three children, and it gives me great happiness to share it with your family!</p>
  </section>

  <svg class="scene" viewBox="0 0 799 927">
    <defs>
      <linearGradient id="sceneTone" x1="0" y1="0" x2="1" y2="1">
        <stop offset="0" stop-color="#2b2826"/>
        <stop offset=".45" stop-color="#5a4a40"/>
        <stop offset=".75" stop-color="#9a7d68"/>
        <stop offset="1" stop-color="#c7b09b"/>
      </linearGradient>
    </defs>
    <rect width="799" height="927" fill="url(#sceneTone)" role="img" aria-label="Photo of a smiling couple holding ultrasound prints"/>
    <path d="M0,0 C10,330 170,590 440,625 C600,645 720,660 799,655 L799,927 L0,927 Z" fill="#ffffff"/>
    <path d="M0,0 C10,330 170,590 440,625 C600,645 720,660 799,655" fill="none" stroke="#E54698" stroke-width="18"/>
  </svg>
  <div class="divider"></div>

  <h2 class="packages__title">Home services &amp; Packages</h2>

  <div class="package__photo" style="left:442px;top:102px" role="img" aria-label="3D ultrasound image of a baby's face"></div>
  <div class="package__text" style="top:110px">
    <p class="package__name">Peace of mind</p>
    <p class="package__price">$160</p>
  </div>

  <div class="package__photo" style="left:442px;top:237px" role="img" aria-label="3D ultrasound image of baby feet"></div>
  <div class="package__text" style="top:246px">
    <p class="package__name">Early gender</p>
    <p class="package__price">$160</p>
  </div>

  <div class="package__photo" style="left:442px;top:365px" role="img" aria-label="3D ultrasound image of a sleeping baby"></div>
  <div class="package__text" style="top:374px">
    <p class="package__name">3D/4D imaging</p>
    <p class="package__price">$150</p>
  </div>

  <div class="feature-photo" role="img" aria-label="Large 3D ultrasound image of a baby's face"></div>

  <div class="icon-disc" style="left:434px;top:613px">
    <svg width="26" height="34" viewBox="0 0 26 34" aria-label="Location">
      <path d="M13 1C6.4 1 1 6.2 1 12.6 1 21 13 33 13 33s12-12 12-20.4C25 6.2 19.6 1 13 1z" fill="#fff"/>
      <circle cx="13" cy="12.5" r="4.6" fill="#E54698"/>
    </svg>
  </div>
  <p class="contact__address">14 Linden Ave, Troy,<br>New York 12180</p>

  <div class="icon-disc" style="left:434px;top:786px">
    <svg width="30" height="30" viewBox="0 0 24 24" aria-label="Phone">
      <path d="M6.6 10.8a15.1 15.1 0 0 0 6.6 6.6l2.2-2.2c.3-.3.7-.4 1-.2 1.1.4 2.3.6 3.6.6.6 0 1 .4 1 1V20c0 .6-.4 1-1 1C10.6 21 3 13.4 3 4c0-.6.4-1 1-1h3.5c.6 0 1 .4 1 1 0 1.3.2 2.5.6 3.6.1.3 0 .7-.2 1z" fill="#fff"/>
    </svg>
  </div>
  <p class="contact__phone">518-555-0142</p>

  <h1 class="cover__title">Professional In-Home<br>3D/4D Ultrasound<br><span class="cover__tagline">Service: My home or Yours!</span></h1>

  <div class="brand">
    <p class="brand__name">Roaming Bump<br>Ultrasound</p>
  </div>

  <p class="call__label">Call Us</p>
  <p class="call__number">518-555-0142</p>

</div>
</body>
</html>
```